A 1 to 2 page digital flyer, using my existing logo and branding files.

I need a professional1 to 2 page flyer in both digital file and an editable PDF form to advertise service offerings for my coaching and consulting business.
The flyer should be upmarket, professional and conservative in style to meet the expectations of my professional market (doctors, psychologists and executives).
It will be based on my existing logo and brand, see my current website: www.marlowadvisory.net
Here are the key elements needed:
1) First the main product offering (which I should be able to edit myself for future use). In this first case, this features an advertisement for a 'Therapy group for professionals'. (see attached file).
2) The second key text is my bio/profile which includes a photo.
3) The third section is a call to action, including my contact details.
4) The flyer should include my email, website and phone contact details.
5) It should also include some small logos of my professional accrediting organisations.

Target Market(s)

Doctors, psychologists, executives in healthcare.

Industry/Entity Type

Health care and business schools

Font styles to use
Other font styles liked:
• Operetta (headings), Sofia Pro (body text).

Colors
0054AA
0677BA
7BADD7
CADEEF
E8F1F8

Requirements
Must have
• 1. Strong adherence to my brand voice and design elements, as featured on my website and in my branded stationery. 2. Editable text sections in PDF that I can re-use for future advertisements. 3. Suitable size and medium (e.g. A4 size) for sharing digitally via my website, email, and social media. 4) Very prompt design as soon as possible please - quick turnaround will secure the winning place.
Nice to have
• Please use design images and inspiration from my website. An additional stock photo of a therapy group is uploaded as an example
Should not have
• Do not deviate from my brand voice, fonts and colours please.

```html
<!DOCTYPE html>
<html lang="en">
<head>
<meta charset="utf-8">
<title>Marlow Advisory – Therapy Group Flyer</title>
<link rel="stylesheet" href="https://fonts.googleapis.com/css2?family=Playfair+Display:wght@400;600&family=Mulish:wght@400;600;700&display=swap">
<style>
:root{
  --brand-deep:#0054AA;
  --brand-mid:#0677BA;
  --brand-soft:#7BADD7;
  --brand-pale:#CADEEF;
  --brand-mist:#E8F1F8;
  --ink:#3a4350;
  --paper:#ffffff;
  --backdrop:#eef0f3;
}
*{margin:0;padding:0;box-sizing:border-box}
html,body{width:800px;height:1200px;overflow:hidden;background:var(--backdrop)}
body{position:relative;font-family:'Mulish',sans-serif;color:var(--ink)}
.page{position:absolute;left:191px;width:417px;height:590px;background:var(--paper);overflow:hidden;box-shadow:0 2px 8px rgba(0,0,0,.12)}
.page--offer{top:5px}
.page--profile{top:605px}
.abs{position:absolute}
.brand{display:flex;align-items:center;gap:6px;font-family:'Mulish',sans-serif;font-weight:700;font-size:11px;color:var(--brand-deep);white-space:nowrap}
.brand__mark{width:12px;height:12px;background:var(--brand-mid)}
.heading{font-family:'Playfair Display',serif;color:var(--brand-deep);font-weight:400;line-height:1.05}
.body{font-size:6.6px;line-height:1.5}
.quote-mark{font-family:'Playfair Display',serif;font-size:30px;color:var(--brand-mid);line-height:.8}
.photo{position:absolute}
/* offer page */
.offer__title{left:20px;top:48px;font-size:27px;width:185px}
.offer__intro{left:20px;top:122px;width:175px}
.offer__subtitle{left:20px;top:160px;font-size:15px;width:180px}
.offer__lead{left:20px;top:200px;width:180px}
.offer__building{right:0;top:0;width:205px;height:280px;background:linear-gradient(170deg,#dbe9f5 0%,#9ec3e2 45%,#f3f8fc 80%,#ffffff 100%)}
.offer__quote{left:20px;top:270px;width:180px;border-left:2px solid var(--brand-pale);padding-left:8px}
.offer__quote p{font-style:italic;font-size:7px;line-height:1.5;color:var(--brand-deep)}
.offer__list{left:20px;top:340px;width:180px;list-style:none}
.offer__list li{font-size:6.6px;line-height:1.7;padding-left:9px;position:relative}
.offer__list li::before{content:"";position:absolute;left:0;top:3px;width:4px;height:4px;background:var(--brand-mid)}
.offer__col{left:218px;top:295px;width:180px}
.offer__col h4{font-family:'Playfair Display',serif;font-weight:600;color:var(--brand-deep);font-size:9px;margin-bottom:4px}
.offer__col .body{margin-bottom:10px}
.offer__group{left:0;top:405px;width:205px;height:148px;background:linear-gradient(180deg,#e6e6e6,#9a9a9a)}
.offer__footer{left:0;bottom:0;width:100%;height:37px;background:var(--brand-deep);color:#fff;font-size:9px;font-weight:600;display:flex;align-items:center;justify-content:flex-end;padding-right:22px;letter-spacing:.3px}
.offer__footer::before{content:"";position:absolute;left:0;top:-4px;width:100%;height:4px;background:var(--brand-soft)}
/* profile page */
.profile__title{left:20px;top:20px;font-size:17px;width:195px}
.profile__bio{left:20px;top:110px;width:195px}
.profile__bio p{margin-bottom:7px}
.profile__portrait{right:0;top:18px;width:188px;height:250px;background:linear-gradient(180deg,#c9d9e8 0%,#7f9fbe 55%,#2d4d7a 100%)}
.profile__band{left:0;top:0}
.profile__statement{left:234px;top:322px;width:164px;color:#fff;font-size:8.4px;line-height:1.45;font-weight:600}
.services{left:20px;top:410px;display:flex;gap:16px}
.service{width:56px;text-align:center;font-size:6px;line-height:1.3;color:var(--brand-deep);font-weight:600}
.service__icon{width:34px;height:34px;border-radius:50%;border:1.5px solid var(--brand-mid);margin:0 auto 4px;display:flex;align-items:center;justify-content:center}
.cta{right:20px;top:420px;width:150px;text-align:right}
.cta__button{display:block;background:var(--brand-deep);color:#fff;font-weight:700;font-size:9px;letter-spacing:.8px;padding:7px 0;text-align:center;margin-bottom:8px}
.cta__line{font-size:7.6px;line-height:1.6;color:var(--brand-deep);font-weight:600}
.profile__brand{left:20px;top:540px}
.accreditations{left:150px;top:540px;display:flex;gap:8px}
.badge{width:26px;height:16px;background:var(--brand-pale);border-radius:2px}
</style>
</head>
<body>

<section class="page page--offer">
  <div class="photo offer__building" role="img" aria-label="Glass office tower rising into a pale sky with a water droplet falling into a ripple below"></div>
  <div class="abs brand" style="left:20px;top:18px"><span class="brand__mark"></span>Marlow Advisory</div>
  <h1 class="abs heading offer__title">Transforming<br>Cultures</h1>
  <p class="abs body offer__intro">Creating safe, reflective spaces where professionals can explore the pressures of their work and build healthier cultures.</p>
  <h2 class="abs heading offer__subtitle">A Therapy Group for Professionals</h2>
  <p class="abs body offer__lead">This is a small, closed group for doctors, psychologists and executives who carry heavy responsibility and want a confidential place to reflect, recover and grow.</p>
  <blockquote class="abs offer__quote">
    <div class="quote-mark">“</div>
    <p>Professionals are trained to care for others, yet rarely given room to care for themselves. This group offers that room.</p>
  </blockquote>
  <ul class="abs offer__list">
    <li>Fortnightly evening sessions</li>
    <li>Maximum eight participants</li>
    <li>Led by a registered psychologist</li>
  </ul>
  <div class="abs offer__col">
    <div class="quote-mark">“</div>
    <h4>Who should attend?</h4>
    <p class="body">Senior clinicians and leaders facing burnout, conflict or change, who value depth, discretion and peer support.</p>
    <p class="body">Sessions run over twelve weeks in a private setting. Places are limited and early enquiry is recommended.</p>
  </div>
  <div class="photo offer__group" role="img" aria-label="Black and white photo of a group of professionals seated in a circle"></div>
  <div class="abs offer__footer">www.marlowadvisory.net</div>
</section>

<section class="page page--profile">
  <div class="photo profile__portrait" role="img" aria-label="Portrait of the consultant in a navy suit standing outdoors"></div>
  <svg class="abs profile__band" width="417" height="590" viewBox="0 0 417 590" aria-hidden="true">
    <polygon points="417,240 417,400 210,400 210,300" fill="var(--brand-mid)"/>
    <polygon points="417,250 417,395 222,395 222,305" fill="var(--brand-deep)"/>
    <polygon points="0,565 417,520 417,590 0,590" fill="var(--brand-mist)"/>
    <polygon points="0,580 417,548 417,590 0,590" fill="var(--brand-pale)"/>
  </svg>
  <h1 class="abs heading profile__title">Daniel Marlow – Professor of Organisational Culture and Leadership</h1>
  <div class="abs body profile__bio">
    <p>Daniel is a psychologist and organisational consultant who has spent over twenty years helping leaders build humane, high‑performing workplaces.</p>
    <p>He holds a doctorate in organisational psychology and teaches culture and leadership at leading business schools, combining research with practice.</p>
    <p>His work spans hospitals, universities and corporate teams, guiding them through change with clarity, compassion and evidence.</p>
  </div>
  <p class="abs profile__statement">At Marlow Advisory, we catalyse the deep cultural change needed to create humane, people-centred workplaces.</p>
  <div class="abs services">
    <div class="service"><div class="service__icon"><svg width="16" height="16" viewBox="0 0 16 16"><circle cx="8" cy="5" r="3" fill="none" stroke="#0677BA" stroke-width="1.4"/><path d="M2 15c0-3.5 2.7-5.5 6-5.5s6 2 6 5.5" fill="none" stroke="#0677BA" stroke-width="1.4"/></svg></div>Culture consulting</div>
    <div class="service"><div class="service__icon"><svg width="18" height="16" viewBox="0 0 18 16"><circle cx="5" cy="5" r="2.4" fill="none" stroke="#0677BA" stroke-width="1.3"/><circle cx="13" cy="5" r="2.4" fill="none" stroke="#0677BA" stroke-width="1.3"/><path d="M1 14c0-3 2-4.5 4-4.5s4 1.5 4 4.5M9 14c0-3 2-4.5 4-4.5s4 1.5 4 4.5" fill="none" stroke="#0677BA" stroke-width="1.3"/></svg></div>Group therapy</div>
    <div class="service"><div class="service__icon"><svg width="16" height="16" viewBox="0 0 16 16"><path d="M2 13l4-5 3 3 5-7" fill="none" stroke="#0677BA" stroke-width="1.5"/><path d="M10 4h4v4" fill="none" stroke="#0677BA" stroke-width="1.5"/></svg></div>Leadership coaching</div>
  </div>
  <div class="abs cta">
    <span class="cta__button">BOOK A MEETING</span>
    <div class="cta__line">+61 3 9000 1234</div>
    <div class="cta__line">info@marlowadvisory.net</div>
    <div class="cta__line">www.marlowadvisory.net</div>
  </div>
  <div class="abs brand profile__brand"><span class="brand__mark"></span>Marlow Advisory</div>
  <div class="abs accreditations">
    <span class="badge"></span><span class="badge"></span><span class="badge"></span>
  </div>
</section>

</body>
</html>
```